Brightlane Rapid Rinse Web Design

We are looking for a web design that highlights our state of the art fully automated commercial vehicle washing equipment. Similar system to a car wash however this system is meant for the largest vehicles on our roadways. Transport trucks with or without a trailer, busses both highway and school, RV's from 5th wheel type to A Class. Cement trucks, dump trucks, vac trucks, fuel trucks etc. Pick ups with utility trailers...Refrigerator truck clean outs.
Brightlane Rapid Rinse will wash your vehicle quickly and with a minimal impact on the environment

Home page
About us
Why Brightlane
Services and pricing
Videos of wash system
Fleets
contact us

Target Market(s)

Commercial vehicle owners and operators as well as corporate fleets. Includes busses, municipal, school and highway.both school and

Industry/Entity Type

transportation

Coding

Coded - Design and coding required

Number of Pages Required

5+ page

Font styles to use
Sans Serif

Colors
0054AA
0677BA
7BADD7
CADEEF
E8F1F8

Requirements
Must have
• Welcome page,why us page which describes the financial and environmental benefits. payment processing page, contact us page, Services which is washing vehicles and greasing for commercial vehicles that want that service and grease
Nice to have
• pictures of both clean and dirty commercial vehicles ie. before and after

```html
<!DOCTYPE html>
<html lang="en">
<head>
<meta charset="utf-8">
<title>Brightlane Rapid Rinse</title>
<link href="https://fonts.googleapis.com/css2?family=Poppins:wght@400;500;600;700&family=Lato:wght@400;700&display=swap" rel="stylesheet">
<style>
:root{
  --blue:#0054AA;
  --blue-mid:#0677BA;
  --blue-soft:#7BADD7;
  --blue-pale:#CADEEF;
  --blue-wash:#E8F1F8;
  --ink:#111111;
  --footer:#161618;
  --grey-band:#F1F1F2;
  --white:#ffffff;
}
*{box-sizing:border-box;margin:0;padding:0}
html,body{width:1200px;height:2676px;overflow:hidden}
body{position:relative;font-family:"Lato",sans-serif;color:var(--ink);background:var(--white)}
.abs{position:absolute}
a{color:inherit;text-decoration:none}

.topbar{left:0;top:0;width:1200px;height:51px;background:var(--blue);color:var(--white);font-family:"Poppins",sans-serif;font-size:13px}
.topbar .item{top:16px;display:flex;align-items:center;gap:8px}

.nav{left:0;top:51px;width:1200px;height:85px;background:var(--white)}
.brand{font-family:"Poppins",sans-serif;font-weight:600;font-size:22px;letter-spacing:.3px;color:var(--ink)}
.nav .brand{left:93px;top:32px}
.menu{top:36px;font-family:"Poppins",sans-serif;font-size:15px;color:var(--ink)}
.menu.active{color:var(--blue);text-decoration:underline;text-underline-offset:4px}
.nav .cta{left:987px;top:27px;width:120px;height:39px;border:1px solid var(--blue);color:var(--blue);font-family:"Poppins",sans-serif;font-size:14px;display:flex;align-items:center;justify-content:center}

.hero{left:0;top:136px;width:1200px;height:577px;background:linear-gradient(110deg,#8a8f92 0%,#b07a45 28%,#7e7f78 50%,#c9b9a6 70%,#d6dde6 100%)}
.hero-frame{left:218px;top:104px;width:764px;height:392px;border:2px solid var(--white);background:rgba(40,40,45,.45);text-align:center;color:var(--white);font-family:"Poppins",sans-serif}
.hero-frame .kicker{margin-top:30px;font-size:26px;font-weight:600}
.hero-frame .title{font-size:56px;font-weight:700;letter-spacing:1px;line-height:1.1;margin-top:8px}
.hero-frame .sub{font-size:20px;font-weight:600;margin-top:14px}
.hero-frame .btns{display:flex;justify-content:center;gap:26px;margin-top:34px}
.btn{width:188px;height:60px;display:flex;align-items:center;justify-content:center;font-size:20px;font-weight:600}
.btn.solid{background:var(--white);color:var(--blue)}
.btn.ghost{border:3px solid var(--white);color:var(--white)}
.arrow-dot{width:31px;height:31px;border-radius:50%;background:var(--ink);display:flex;align-items:center;justify-content:center}

.mission{left:0;top:713px;width:1200px;height:539px;background:var(--blue);color:var(--white)}
.mission-photo{left:112px;top:780px;width:406px;height:536px;border:3px solid var(--white);background:linear-gradient(135deg,#d8b58c 0%,#9b6a48 45%,#3c3a3a 100%)}
.mission h2{left:598px;top:58px;font-family:"Poppins",sans-serif;font-size:33px;font-weight:600}
.mission .lead{left:599px;top:112px;width:500px;font-weight:700;font-size:16px;line-height:28px}
.mission .body{left:600px;width:488px;font-size:15px;line-height:27.5px;text-align:justify}
.mission .read{left:600px;top:412px;width:144px;height:51px;background:var(--white);color:var(--blue);font-family:"Poppins",sans-serif;font-weight:500;font-size:18px;display:flex;align-items:center;justify-content:center}

.services-title{left:0;top:1368px;width:1200px;text-align:center;font-family:"Poppins",sans-serif;font-weight:600;font-size:37px;color:var(--blue)}
.card{top:1445px;width:310px;height:339px}
.card .photo{position:absolute;inset:0}
.card .label{position:absolute;left:0;bottom:0;width:310px;height:60px}
.card .label span{position:absolute;left:21px;top:18px;font-size:19px;color:var(--white)}

.compare{left:0;top:1852px;width:1200px;height:409px;background:var(--grey-band)}
.shot{top:64px;width:476px;height:273px}
.tag{position:absolute;left:14px;top:14px;padding:6px 14px;background:var(--white);color:var(--blue);font-family:"Poppins",sans-serif;font-weight:500;font-size:17px}

.footer{left:0;top:2261px;width:1200px;height:415px;background:var(--footer);color:var(--white)}
.footer .brand{left:110px;top:72px;color:var(--white)}
.social{top:150px;width:32px;height:32px;border-radius:50%;background:var(--white)}
.fhead{top:71px;font-family:"Poppins",sans-serif;font-size:19px}
.links{top:117px;list-style:none;font-size:15px;line-height:34.5px}
.links li{display:flex;align-items:center;gap:10px}
.contact-row{left:831px;display:flex;gap:12px;font-size:15px;line-height:27px}
.contact-row .ic{width:32px;height:32px;border-radius:50%;background:var(--white);display:flex;align-items:center;justify-content:center;flex:none}
.footer .rule{left:112px;top:317px;width:978px;height:1px;background:#cfcfcf}
.footer .copy{left:0;top:2618px;width:1200px}
.copyright{left:0;top:352px;width:1200px;text-align:center;font-size:16px;font-weight:700}
.bottom-strip{left:0;top:2668px;width:1200px;height:8px;background:var(--blue)}
</style>
</head>
<body>

<header class="abs topbar">
  <div class="abs item" style="left:589px">
    <svg width="12" height="12" viewBox="0 0 24 24"><path fill="#fff" d="M6.6 10.8a15 15 0 006.6 6.6l2.2-2.2a1 1 0 011-.25 11.4 11.4 0 003.6.57 1 1 0 011 1V20a1 1 0 01-1 1A17 17 0 013 4a1 1 0 011-1h3.5a1 1 0 011 1c0 1.25.2 2.45.57 3.6a1 1 0 01-.25 1z"/></svg>
    <span>Phone : +1 555 014 2290</span>
  </div>
  <div class="abs" style="left:781px;top:15px">|</div>
  <div class="abs item" style="left:810px">
    <svg width="14" height="11" viewBox="0 0 24 18"><path fill="#fff" d="M0 0h24v18H0z"/><path fill="#0054AA" d="M1 1l11 8 11-8v2L12 11 1 3z"/></svg>
    <span>Email : info@brightlanerinse.com</span>
  </div>
</header>

<nav class="abs nav">
  <div class="abs brand">BRIGHTLANE RAPID RINSE</div>
  <a class="abs menu active" style="left:476px">HOME</a>
  <a class="abs menu" style="left:567px">ABOUT US</a>
  <a class="abs menu" style="left:688px">WHY BRIGHTLANE</a>
  <a class="abs menu" style="left:893px">MORE</a>
  <a class="abs cta">CONTACT US</a>
</nav>

<section class="abs hero" role="img" aria-label="Worker in hi-vis jacket pressure washing a large orange refuse truck">
  <div class="abs hero-frame">
    <div class="kicker">WELCOME TO</div>
    <div class="title">BRIGHTLANE RAPID</div>
    <div style="font-size:26px;letter-spacing:8px;margin-top:4px">RINSE</div>
    <div class="sub">SPEED (LESS THAN 15 MINUTES)</div>
    <div class="btns">
      <a class="btn solid">BOOK A WASH</a>
      <a class="btn ghost">LEARN MORE</a>
    </div>
  </div>
  <div class="abs arrow-dot" style="left:1130px;top:271px">
    <svg width="12" height="14" viewBox="0 0 12 14"><path d="M3 1l6 6-6 6" stroke="#fff" stroke-width="2.2" fill="none"/></svg>
  </div>
</section>

<section class="abs mission">
  <h2 class="abs">OUR MISSION</h2>
  <p class="abs lead">Our dedication to revolutionizing truck washing with advanced technology and sustainable practices,</p>
  <p class="abs body" style="top:178px">At vero eos et accusamus et iusto odio dignissimos ducimus quiblan tiis pti nimi, id est laborum et dolorum fuga.</p>
  <p class="abs body" style="top:260px">Temporibus autem quibusdam et aut officiis debitisert autitr rerum necessaibus saepe eveniet ut et voluptates repuderaer iandae moles non recundae. Itaque earum rerum hic tenetuapiente deleus, ut aut reiciendis voluptatibus maiores alias consequatur aut perferendis doloribus asperiores repellat.</p>
  <a class="abs read">READ MORE</a>
</section>
<div class="abs mission-photo" role="img" aria-label="Man in cap and plaid shirt pressure washing truck wheels"></div>

<h2 class="abs services-title">OUR SERVICES</h2>
<div class="abs card" style="left:111px">
  <div class="photo" role="img" aria-label="Truck inside an automated wash bay with red and black brushes" style="background:linear-gradient(90deg,#2a1f24 0%,#b0252f 20%,#dfe1e4 40%,#c8ccd2 60%,#b0252f 80%,#2a1f24 100%)"></div>
  <div class="label"><svg width="310" height="60"><path d="M0 0h245l65 60H0z" fill="#0054AA"/></svg><span>Automated Truck Wash</span></div>
</div>
<div class="abs card" style="left:446px">
  <div class="photo" role="img" aria-label="Worker washing beside a white truck cab in a wash hall" style="background:linear-gradient(90deg,#d9dde0 0%,#8e9396 35%,#e9ecee 65%,#bfc4c8 100%)"></div>
  <div class="label"><svg width="310" height="60"><path d="M0 0h235l75 60H0z" fill="#0054AA"/></svg><span>Additional Services</span></div>
</div>
<div class="abs card" style="left:778px">
  <div class="photo" role="img" aria-label="Row of white fleet trucks parked at sunset" style="background:linear-gradient(180deg,#c7d3e0 0%,#e8cfb8 35%,#a5adb5 65%,#4d5358 100%)"></div>
  <div class="label"><svg width="310" height="60"><path d="M0 0h235l60 60H0z" fill="#0054AA"/></svg><span>Fleet Services</span></div>
</div>

<section class="abs compare">
  <div class="abs arrow-dot" style="left:33px;top:188px;background:#7a7a7a">
    <svg width="12" height="14" viewBox="0 0 12 14"><path d="M9 1L3 7l6 6" stroke="#fff" stroke-width="2.2" fill="none"/></svg>
  </div>
  <div class="abs shot" style="left:111px" role="img" aria-label="Dirty truck front covered in wash foam">
    <div style="position:absolute;inset:0;background:linear-gradient(135deg,#d6dbe1 0%,#9aa3ad 50%,#5b6570 100%)"></div>
    <span class="tag">BEFORE</span>
  </div>
  <div class="abs shot" style="left:614px" role="img" aria-label="Clean tanker truck being rinsed with a pressure washer">
    <div style="position:absolute;inset:0;background:linear-gradient(135deg,#8fa0ad 0%,#c9cdd0 45%,#e6e6e4 70%,#7e858a 100%)"></div>
    <span class="tag">AFTER</span>
  </div>
  <div class="abs arrow-dot" style="left:1130px;top:188px">
    <svg width="12" height="14" viewBox="0 0 12 14"><path d="M3 1l6 6-6 6" stroke="#fff" stroke-width="2.2" fill="none"/></svg>
  </div>
</section>

<footer class="abs footer">
  <div class="abs brand">BRIGHTLANE RAPID RINSE</div>
  <div class="abs social" style="left:117px" aria-label="Social link"></div>
  <div class="abs social" style="left:175px" aria-label="Social link"></div>
  <div class="abs social" style="left:233px" aria-label="Social link"></div>
  <div class="abs social" style="left:290px" aria-label="Social link"></div>

  <h3 class="abs fhead" style="left:436px;font-weight:400">QUICK LINKS</h3>
  <ul class="abs links" style="left:437px">
    <li><svg width="13" height="11" viewBox="0 0 13 11"><path d="M0 5.5h9M6 1l5 4.5L6 10" stroke="#fff" stroke-width="2" fill="none"/></svg>Home</li>
    <li><svg width="13" height="11" viewBox="0 0 13 11"><path d="M0 5.5h9M6 1l5 4.5L6 10" stroke="#fff" stroke-width="2" fill="none"/></svg>About us</li>
    <li><svg width="13" height="11" viewBox="0 0 13 11"><path d="M0 5.5h9M6 1l5 4.5L6 10" stroke="#fff" stroke-width="2" fill="none"/></svg>Why Brightlane</li>
    <li><svg width="13" height="11" viewBox="0 0 13 11"><path d="M0 5.5h9M6 1l5 4.5L6 10" stroke="#fff" stroke-width="2" fill="none"/></svg>Services and pricing</li>
    <li><svg width="13" height="11" viewBox="0 0 13 11"><path d="M0 5.5h9M6 1l5 4.5L6 10" stroke="#fff" stroke-width="2" fill="none"/></svg>Videos of wash system</li>
  </ul>

  <h3 class="abs fhead" style="left:655px;font-weight:400">HELP LINKS</h3>
  <ul class="abs links" style="left:655px">
    <li><svg width="13" height="11" viewBox="0 0 13 11"><path d="M0 5.5h9M6 1l5 4.5L6 10" stroke="#fff" stroke-width="2" fill="none"/></svg>FAQ</li>
    <li><svg width="13" height="11" viewBox="0 0 13 11"><path d="M0 5.5h9M6 1l5 4.5L6 10" stroke="#fff" stroke-width="2" fill="none"/></svg>Terms of use</li>
    <li><svg width="13" height="11" viewBox="0 0 13 11"><path d="M0 5.5h9M6 1l5 4.5L6 10" stroke="#fff" stroke-width="2" fill="none"/></svg>Privacy Policy</li>
    <li><svg width="13" height="11" viewBox="0 0 13 11"><path d="M0 5.5h9M6 1l5 4.5L6 10" stroke="#fff" stroke-width="2" fill="none"/></svg>Support Links</li>
    <li><svg width="13" height="11" viewBox="0 0 13 11"><path d="M0 5.5h9M6 1l5 4.5L6 10" stroke="#fff" stroke-width="2" fill="none"/></svg>Conditions</li>
  </ul>

  <h3 class="abs fhead" style="left:830px;font-weight:400">CONTACT US</h3>
  <div class="abs contact-row" style="top:116px">
    <span class="ic"><svg width="14" height="18" viewBox="0 0 14 18"><path d="M7 0a7 7 0 00-7 7c0 5 7 11 7 11s7-6 7-11a7 7 0 00-7-7z" fill="#161618"/><circle cx="7" cy="7" r="2.5" fill="#fff"/></svg></span>
    <span>Brightlane Rapid Rinse<br>United States</span>
  </div>
  <div class="abs contact-row" style="top:178px">
    <span class="ic"><svg width="15" height="15" viewBox="0 0 24 24"><path fill="#161618" d="M6.6 10.8a15 15 0 006.6 6.6l2.2-2.2a1 1 0 011-.25 11.4 11.4 0 003.6.57 1 1 0 011 1V20a1 1 0 01-1 1A17 17 0 013 4a1 1 0 011-1h3.5a1 1 0 011 1c0 1.25.2 2.45.57 3.6a1 1 0 01-.25 1z"/></svg></span>
    <span style="padding-top:3px">+1 555 014 2290</span>
  </div>
  <div class="abs contact-row" style="top:230px">
    <span class="ic"><svg width="15" height="11" viewBox="0 0 24 18"><path fill="#161618" d="M0 0h24v18H0z"/><path fill="#fff" d="M1 1l11 8 11-8v2L12 11 1 3z"/></svg></span>
    <span style="padding-top:3px">info@brightlanerinse.com</span>
  </div>

  <div class="abs rule"></div>
  <p class="abs copyright">Copyrights@2024.Brightlane Rapid Rinse.All Rights Reserved</p>
</footer>
<div class="abs bottom-strip"></div>

</body>
</html>
```